Web Site Design for a Finance (lending) Company

We are opening a new subsidiary that focuses on lending money in the real estate industry. We need a web site designed to represent the business.

The business is lending money to real estate investors. A typical client/borrower will be looking to borrow money to buy a house, renovate it and then sell it at a profit, all within 12 months or less.

Company name is RTV Finance. Our logo is attached.

Attached is a general outline for the web site. We're working on writing more text for each page but this should give you enough to get started with some ideas.

Competitor web site that I like a lot (as an example): https://dorvaleqcapital.example/. Many of the general items on this site match what we will need (description of loan programs, FAQ)

Target Market(s)

Real estate investors (generally individuals or small companies with just a few people) who are buying homes, renovating them and then selling them at a profit.

Industry/Entity Type

Finance

Coding

Coded - Design and coding required

Number of Pages Required

5+ page

Colors

Designer to choose colors to be used in the design.

Requirements
Must have
• Minimalist design. Clean lines without too much clutter. Some stock photography is ok but the photos should not be distracting. They should almost fade in to the background so that user can focus on the key information about what our company does instead. We are a finance company, not a design company, so the information about our products will be more interesting to site visitors than the art.
• Some minimalist examples from Snapboard:
• https://www.snapboardia.example/explore/minimalist-web-design/
Nice to have
• If you search in zoovle for "hard money lenders" you will find many examples of web sites from our competition. I have provided a link above to competitor web site that I like a lot.
• I have attached our logo in EPS format. Logo is green. Web site doesn't have to be green but it should be of a color that will work well with the logo.

```html
<!DOCTYPE html>
<html lang="en">
<head>
<meta charset="utf-8">
<title>RTV Finance – Real Estate Lending</title>
<link rel="stylesheet" href="https://fonts.googleapis.com/css2?family=Poppins:wght@400;500;600;700&family=Open+Sans:wght@400;600&display=swap">
<style>
:root{
  --green:#0d5b3b;
  --green-dark:#083f29;
  --green-soft:#2f7a57;
  --ink:#1f1f1f;
  --muted:#9a9a9a;
  --line:#d7d7d7;
  --panel:#ececec;
  --footer:#efefef;
  --white:#ffffff;
  --sky-top:#2a47cc;
  --sky-mid:#2a3d9e;
  --dusk:#3b2d22;
}
*{box-sizing:border-box;margin:0;padding:0}
html,body{width:1200px;height:4306px;overflow:hidden}
body{position:relative;background:var(--white);font-family:"Open Sans",Arial,sans-serif;color:var(--ink)}
.abs{position:absolute}
.heading{font-family:"Poppins",Arial,sans-serif;font-weight:600;color:var(--ink);text-align:center;width:1200px;left:0}
.section-mark{width:26px;height:26px;border:3px solid var(--green);left:587px}
.body-copy{font-size:12.5px;line-height:21px;color:var(--muted)}
.btn{background:var(--green);color:var(--white);font-family:"Poppins",Arial,sans-serif;font-size:13px;font-weight:600;letter-spacing:.5px;display:flex;align-items:center;justify-content:center}

/* hero */
.hero-photo{left:0;top:0;width:1200px;height:600px;background:linear-gradient(180deg,var(--sky-top) 0%,var(--sky-mid) 38%,#4a4a66 60%,var(--dusk) 100%)}
.brand{display:flex;align-items:center;gap:10px;font-family:"Poppins",Arial,sans-serif;font-weight:500;font-size:22px;line-height:24px}
.brand-box{width:14px;height:14px;background:currentColor}
.hero-brand{left:165px;top:44px;color:var(--white)}
.nav{left:596px;top:60px;display:flex;gap:34px;font-family:"Poppins",Arial,sans-serif;font-size:13px;font-weight:600;color:var(--white)}
.hero-title{left:190px;top:262px;width:640px;text-align:center;font-family:"Poppins",Arial,sans-serif;font-weight:600;font-size:31px;line-height:44px;color:var(--white);text-shadow:0 2px 6px rgba(0,0,0,.45);white-space:nowrap}
.hero-btn{left:431px;top:378px;width:158px;height:42px}
.slide-arrow{left:80px;top:330px}

/* chat */
.chat{left:853px;top:192px;width:347px;height:506px;background:var(--white);border:1px solid var(--line);box-shadow:0 4px 18px rgba(0,0,0,.18)}
.chat-head{height:50px;background:var(--green);display:flex;align-items:center;padding:0 16px;gap:12px;color:var(--white);font-family:"Poppins",Arial,sans-serif;font-weight:600;font-size:16px}
.chat-bubble{width:26px;height:26px;border-radius:50%;border:2px solid var(--white)}
.chat-close{margin-left:auto;font-size:18px}
.chat-agent{left:26px;top:108px;width:48px;height:48px;border-radius:50%;background:linear-gradient(#c9d3dc,#8fa0b1)}
.chat-hello{left:86px;top:122px;font-family:"Poppins",Arial,sans-serif;font-weight:600;font-size:14px;color:var(--green)}
.chat-input{left:22px;top:420px;width:302px;height:46px;border:1px solid var(--line);border-radius:23px;display:flex;align-items:center;padding:0 18px;font-size:11px;color:#777}
.chat-input svg{margin-left:auto}

/* loans */
.card-frame{width:387px;height:279px;border:9px solid #9c9c9c;border-bottom:none;overflow:hidden}
.card-photo{position:absolute;inset:0;background:linear-gradient(160deg,#e7e7e7,#8c8c8c)}
.card-title{font-family:"Poppins",Arial,sans-serif;font-weight:600;font-size:27px;text-align:center;width:387px}
.card-copy{width:387px;text-align:center}

/* why */
.feature{width:260px}
.feature-icon{width:70px;height:56px;border:1px solid #bdbdbd;display:flex;align-items:center;justify-content:center}
.feature-label{font-family:"Poppins",Arial,sans-serif;font-weight:600;font-size:14px;margin-top:15px}
.feature-copy{margin-top:26px;width:240px}

/* testimonial */
.quote-name{left:502px;top:3010px;font-family:"Poppins",Arial,sans-serif;font-weight:600;font-size:15px;color:var(--white)}
.quote-copy{left:502px;top:3054px;width:470px;font-size:12.5px;line-height:20px;color:#d8e6de}
.quote-face{left:298px;top:2994px;width:156px;height:156px;border-radius:50%;border:6px solid var(--white);background:linear-gradient(#dfe5ea,#a9b6c2)}

/* memberships */
.member-badge{top:3556px;height:78px}

/* footer */
.footer{left:0;top:3732px;width:1200px;height:508px;background:var(--footer)}
.foot-head{font-family:"Poppins",Arial,sans-serif;font-weight:600;font-size:13px;color:var(--green)}
.foot-list{list-style:none;margin-top:22px;font-size:12.5px;line-height:23.5px;color:var(--ink)}
.social{left:712px;top:3826px;display:flex;align-items:center;gap:11px}
.social-dot{width:24px;height:24px;border-radius:50%;background:#8a8a8a}
.social-dot.first{background:var(--green)}
.form{left:537px;top:3899px;width:488px;height:236px;background:var(--white);padding:18px 22px}
.field{position:absolute;border-bottom:1px solid var(--line);font-size:10.5px;color:#888;padding-bottom:6px}
.send{left:560px;top:4158px;width:92px;height:34px}
.copyright{left:0;top:4272px;width:1200px;text-align:center;font-family:"Poppins",Arial,sans-serif;font-weight:600;font-size:12px}
</style>
</head>
<body>

<!-- HERO -->
<div class="abs hero-photo" role="img" aria-label="Modern two-storey home with lit windows at dusk under a blue sky"></div>
<svg class="abs" style="left:0;top:0" width="1200" height="600" aria-hidden="true">
  <polygon points="0,440 780,565 0,545" fill="var(--green)"/>
  <polygon points="0,520 1200,545 1200,600 0,600" fill="var(--white)"/>
</svg>
<div class="abs brand hero-brand"><span class="brand-box"></span>RTV Finance</div>
<nav class="abs nav"><span>HOME</span><span>ABOUT US</span><span>LOANS</span><span>RESOURCES</span><span>CONTACT US</span></nav>
<h1 class="abs hero-title">Local real estate experts lending<br>to local real estate investors</h1>
<div class="abs btn hero-btn">LEARN MORE</div>
<svg class="abs slide-arrow" width="14" height="22" aria-hidden="true"><polyline points="12,2 3,11 12,20" fill="none" stroke="#fff" stroke-width="3"/></svg>

<!-- LIVE CHAT -->
<aside class="abs chat">
  <div class="chat-head"><span class="chat-bubble"></span>Welcome to live chat<span class="chat-close">&times;</span></div>
  <div class="abs chat-agent" role="img" aria-label="Support agent portrait"></div>
  <div class="abs chat-hello">Hi, How Can I Help you ?</div>
  <div class="abs chat-input">Type here to Chat With Us
    <svg width="16" height="16" aria-hidden="true"><polygon points="1,8 15,1 11,15 8,9" fill="var(--green)"/></svg>
  </div>
</aside>

<!-- WELCOME -->
<div class="abs section-mark" style="top:660px"></div>
<h2 class="abs heading" style="top:718px;font-size:31px">Welcome to RTV Finance</h2>
<p class="abs body-copy" style="left:200px;top:806px;width:800px;text-align:center;color:#555">RTV Finance is a local business with local knowledge and strong industry relationships. A partner with a wide network who offers value added services. RTV has an established pool of experienced investors available for your real estate investment needs</p>
<div class="abs btn" style="left:522px;top:920px;width:156px;height:44px">READ MORE</div>

<!-- LOANS -->
<svg class="abs" style="left:0;top:1020px" width="1200" height="880" aria-hidden="true">
  <polygon points="0,110 780,5 1200,70 1200,800 0,875" fill="var(--panel)"/>
  <polygon points="760,875 1200,790 1200,812 820,875" fill="#9b9ba3"/>
</svg>
<div class="abs section-mark" style="top:1128px"></div>
<h2 class="abs heading" style="top:1186px;font-size:31px">Loans offered</h2>

<div class="abs card-frame" style="left:187px;top:1329px">
  <div class="card-photo" role="img" aria-label="Investor holding a small house model"></div>
  <svg class="abs" style="left:-9px;bottom:0" width="387" height="60" aria-hidden="true"><polygon points="0,60 0,40 387,20 387,60" fill="var(--green)"/></svg>
</div>
<div class="abs card-title" style="left:187px;top:1628px">Fix and Flip</div>
<p class="abs body-copy card-copy" style="left:187px;top:1700px">Short-term loans for investors who buy, renovate and resell homes. Quick approvals, clear terms and a local team that helps each project move from purchase to a profitable sale.</p>

<div class="abs card-frame" style="left:626px;top:1329px">
  <div class="card-photo" role="img" aria-label="Commercial office towers in grey tones"></div>
  <svg class="abs" style="left:-9px;bottom:0" width="387" height="60" aria-hidden="true"><polygon points="0,60 0,40 387,20 387,60" fill="var(--green)"/></svg>
</div>
<div class="abs card-title" style="left:626px;top:1628px">Commercial</div>
<p class="abs body-copy card-copy" style="left:626px;top:1700px">Flexible financing for small commercial properties, mixed-use buildings and rentals. We review each deal on its merits and fund quickly so you can close with confidence and start earning sooner.</p>

<!-- WHY BORROW -->
<div class="abs section-mark" style="top:2005px"></div>
<h2 class="abs heading" style="top:2068px;font-size:31px">Why borrow from RTV</h2>

<div class="abs feature" style="left:172px;top:2190px">
  <div class="feature-icon"><svg width="30" height="34" aria-hidden="true"><circle cx="15" cy="12" r="9" fill="none" stroke="var(--green)" stroke-width="2"/><polyline points="9,19 7,32 15,27 23,32 21,19" fill="none" stroke="var(--green)" stroke-width="2"/></svg></div>
  <div class="feature-label">Experts</div>
  <p class="body-copy feature-copy">Our team has financed hundreds of local homes and knows what makes a renovation project succeed.</p>
</div>
<div class="abs feature" style="left:465px;top:2190px">
  <div class="feature-icon"><svg width="34" height="28" aria-hidden="true"><rect x="1" y="1" width="32" height="26" fill="none" stroke="var(--green)" stroke-width="2"/><path d="M8 20a9 9 0 0 1 18 0" fill="none" stroke="var(--green)" stroke-width="2"/><line x1="17" y1="20" x2="22" y2="13" stroke="var(--green)" stroke-width="2"/></svg></div>
  <div class="feature-label">Fast Approval</div>
  <p class="body-copy feature-copy">Send us your deal today and receive a clear answer within days, not weeks, with funding ready to go.</p>
</div>
<div class="abs feature" style="left:758px;top:2190px">
  <div class="feature-icon"><svg width="34" height="32" aria-hidden="true"><circle cx="17" cy="8" r="6" fill="none" stroke="var(--green)" stroke-width="2"/><path d="M6 30a11 11 0 0 1 22 0" fill="none" stroke="var(--green)" stroke-width="2"/></svg></div>
  <div class="feature-label">Professional</div>
  <p class="body-copy feature-copy">Straightforward terms, honest communication and careful service from the first call through the final payoff.</p>
</div>
<div class="abs feature" style="left:172px;top:2436px">
  <div class="feature-icon"><svg width="34" height="30" aria-hidden="true"><rect x="1" y="1" width="32" height="28" fill="none" stroke="var(--green)" stroke-width="2"/><circle cx="17" cy="12" r="5" fill="none" stroke="var(--green)" stroke-width="2"/><line x1="8" y1="24" x2="26" y2="24" stroke="var(--green)" stroke-width="2"/></svg></div>
  <div class="feature-label">A Partner</div>
  <p class="body-copy feature-copy">We work beside you on every project and share contacts, advice and support whenever you need it.</p>
</div>
<div class="abs feature" style="left:465px;top:2436px">
  <div class="feature-icon"><svg width="30" height="32" aria-hidden="true"><rect x="1" y="1" width="28" height="30" fill="none" stroke="var(--green)" stroke-width="2"/><line x1="7" y1="10" x2="23" y2="10" stroke="var(--green)" stroke-width="2"/><line x1="7" y1="16" x2="23" y2="16" stroke="var(--green)" stroke-width="2"/><line x1="7" y1="22" x2="17" y2="22" stroke="var(--green)" stroke-width="2"/></svg></div>
  <div class="feature-label">Selective</div>
  <p class="body-copy feature-copy">We choose our projects with care, so every borrower gets full attention and a lender they can trust.</p>
</div>
<div class="abs feature" style="left:758px;top:2436px">
  <div class="feature-icon"><svg width="34" height="30" aria-hidden="true"><rect x="1" y="1" width="32" height="28" fill="none" stroke="var(--green)" stroke-width="2"/><rect x="7" y="16" width="5" height="9" fill="var(--green)"/><rect x="15" y="11" width="5" height="14" fill="var(--green)"/><rect x="23" y="6" width="5" height="19" fill="var(--green)"/></svg></div>
  <div class="feature-label">Competitive Rates &amp; Fees</div>
  <p class="body-copy feature-copy">Fair rates and simple fees with no hidden costs, so you can plan your budget and protect your profit.</p>
</div>

<!-- TESTIMONIALS -->
<svg class="abs" style="left:0;top:2705px" width="1200" height="600" role="img" aria-label="Faded modern house in green tones behind testimonials">
  <defs><linearGradient id="testimonialTone" x1="0" y1="0" x2="1" y2="1"><stop offset="0" stop-color="var(--green-soft)"/><stop offset="1" stop-color="var(--green-dark)"/></linearGradient></defs>
  <polygon points="0,120 880,8 1200,60 1200,395 1000,430 330,580 0,555" fill="url(#testimonialTone)"/>
  <polygon points="330,580 1200,395 1200,420 420,590" fill="var(--white)"/>
</svg>
<h2 class="abs heading" style="top:2866px;font-size:31px;color:var(--white)">Testimonials</h2>
<div class="abs quote-face" role="img" aria-label="Client portrait"></div>
<div class="abs quote-name">Daniel Harlow</div>
<p class="abs quote-copy">RTV Finance made our first flip easy. The team explained every step, approved our loan quickly and stayed in touch until the house sold. We finished on time, under budget and are already planning our next project with them.</p>

<!-- MEMBERSHIPS -->
<div class="abs section-mark" style="top:3372px"></div>
<h2 class="abs heading" style="top:3432px;font-size:31px">Industry Membership Logos</h2>
<div class="abs member-badge" style="left:166px;width:240px;background:#8d8d8d" role="img" aria-label="Membership badge"></div>
<div class="abs member-badge" style="left:445px;width:224px;background:#9a9a9a" role="img" aria-label="Membership badge"></div>
<div class="abs member-badge" style="left:712px;width:160px;background:#7e7e7e" role="img" aria-label="Membership badge"></div>
<div class="abs member-badge" style="left:916px;width:124px;background:#555" role="img" aria-label="Membership badge"></div>

<!-- FOOTER -->
<footer class="abs footer"></footer>
<div class="abs brand" style="left:158px;top:3812px;color:var(--green)"><span class="brand-box"></span>RTV Finance</div>
<div class="abs social">
  <span class="foot-head" style="color:var(--ink)">Social Links</span>
  <span class="social-dot first"></span><span class="social-dot"></span><span class="social-dot"></span><span class="social-dot"></span><span class="social-dot"></span><span class="social-dot"></span>
</div>
<div class="abs" style="left:158px;top:3914px">
  <div class="foot-head">Quick Links</div>
  <ul class="foot-list"><li>Home</li><li>About Us</li><li>Loans</li><li>Resources</li><li>Contact Us</li></ul>
</div>
<div class="abs" style="left:359px;top:3914px">
  <div class="foot-head">Other Links</div>
  <ul class="foot-list"><li>Terms Of Use</li><li>Privacy Policy</li><li>Help</li><li>Disclaimer</li></ul>
</div>
<form class="abs form">
  <div class="foot-head">Contact Us</div>
  <div class="field" style="left:22px;top:60px;width:210px">First Name</div>
  <div class="field" style="left:256px;top:60px;width:210px">Last Name</div>
  <div class="field" style="left:22px;top:104px;width:210px">E-mail</div>
  <div class="field" style="left:256px;top:104px;width:210px">Phone</div>
  <div class="field" style="left:22px;top:148px;width:444px;height:64px">How can we help you?</div>
</form>
<div class="abs btn send">SEND</div>
<div class="abs copyright">© 2017 Company Name &nbsp;|&nbsp; All Rights Reserved</div>

</body>
</html>
```